Pup Snack Den - New Website Design

Create a professional Storvana website for a the hottest trend; a Pup Snack Den subscription box business. Storvana.com is an easy to use website builder.
Please see frellonbox.com; gummotrove.com and wagcrate.com for the concept I am after. The business has not been launched yet, I am currently in the pre-launch stage using a specialized landing page website, and so the time scale for developing my professional looking Storvana website is up to 1-2 weeks.
The webpage should have a fun feel and should match the style of the company logo at gummotrove.com. The pages to include are 'Home', 'About us' and 'Get Started'
Thank you and good luck!

```html
<!DOCTYPE html>
<html lang="en">
<head>
<meta charset="utf-8">
<title>Pup Snack Den</title>
<link href="https://fonts.googleapis.com/css2?family=Mulish:ital,wght@0,300;0,400;0,600;0,700;1,400&display=swap" rel="stylesheet">
<style>
:root{
  --blue:#27b4d9;
  --orange:#ff8a00;
  --ink:#222;
  --body:#777;
  --white:#fff;
  --footer:#eeeeee;
  --line:#bdbdbd;
}
*{box-sizing:border-box;margin:0;padding:0}
html,body{width:1200px;height:4534px;overflow:hidden}
body{font-family:"Mulish",sans-serif;color:var(--ink);background:var(--white);position:relative}
.abs{position:absolute}
.photo{position:absolute}
p{font-size:15px;line-height:24px;color:var(--body)}

/* hero */
.hero{position:absolute;left:0;top:0;width:1200px;height:629px;background:linear-gradient(180deg,#6d5b4f 0%,#8a6b52 50%,#5a3c28 100%)}
.hero .menu{left:130px;top:56px}
.hero .bag{left:1040px;top:50px}
.brand{position:absolute;left:0;right:0;top:48px;text-align:center;color:var(--white);font-size:30px;letter-spacing:1px}
.brand b{font-weight:700}
.hero-title{position:absolute;left:0;right:0;top:248px;text-align:center;color:var(--white);font-size:42px;line-height:50px;font-weight:400}
.dots{position:absolute;left:556px;top:586px;display:flex;gap:8px}
.dots span{width:14px;height:14px;border-radius:50%;background:var(--white)}
.dots span.on{background:transparent;border:2px solid var(--white)}

/* about */
.about-photo{left:187px;top:680px;width:262px;height:262px;border-radius:50%;border:6px solid #ddd;background:radial-gradient(circle,#b58a5a 0%,#d8c3a8 55%,#f3f3f3 100%)}
.rule{position:absolute;height:4px}
.rule.blue{background:var(--blue)}
.rule.orange{background:var(--orange)}
h2{font-weight:400;font-size:34px;line-height:42px}
.about h2{color:var(--blue)}

/* video */
.video{left:0;top:1043px;width:1200px;height:478px;background:linear-gradient(135deg,#5a6b3a 0%,#8a7a66 45%,#4f5f34 100%)}
.video-quote{position:absolute;left:200px;right:200px;top:1176px;text-align:center;color:var(--white);font-size:26px;line-height:38px}
.play{left:552px;top:1269px}

/* why */
.center{text-align:center}

/* tiles */
.tile{top:1860px;width:600px;height:444px}
.tile.left{left:0;background:linear-gradient(135deg,#1fa6cf,#5ec7e4)}
.tile.right{left:600px;background:linear-gradient(135deg,#5a7a3a,#9bb070 60%,#6a8a48)}
.tile-label{position:absolute;left:0;right:0;top:254px;text-align:center;color:var(--white);font-size:25px;letter-spacing:.5px}
.tile svg{position:absolute;left:262px;top:170px}

/* quote band */
.band{left:0;top:2304px;width:1200px;height:302px;background:var(--orange)}
.band-quote{position:absolute;left:0;right:0;top:96px;text-align:center;color:var(--white);font-size:20px;line-height:34px;font-style:italic}
.band-author{position:absolute;left:0;right:0;top:178px;text-align:center;color:var(--white);font-size:20px;font-weight:700}

/* product */
.lead{left:220px;width:760px;top:2656px;text-align:center;font-size:19px;line-height:34px;color:#333}
.bone{left:0;top:2645px;width:190px;height:200px;background:linear-gradient(135deg,#ff3fb2,#e0157f)}
.rope{left:968px;top:2858px;width:232px;height:256px;background:linear-gradient(135deg,#f0a0b8,#7a6a5a)}
.box-frame{left:293px;top:2866px;width:611px;height:284px;border:2px solid #bdbdbd;background:var(--white)}
.pup-peek{left:529px;top:2742px;width:142px;height:145px;background:linear-gradient(180deg,#d8c8b0,#6a4a32);border-radius:40% 40% 10% 10%}
.product{left:187px;top:2902px;width:282px;height:212px;background:linear-gradient(180deg,#c83838 0%,#3aa04a 35%,#c89a62 60%,#b07a44 100%)}
.box-title{left:547px;top:2930px;color:var(--blue);font-size:28px;font-weight:400}
.box-copy{left:547px;top:2980px;width:320px;font-size:13px;line-height:21px}
.btn{position:absolute;display:flex;align-items:center;justify-content:center;color:var(--white);font-size:14px;letter-spacing:.5px}
.btn.orange{background:var(--orange)}
.btn.blue{background:var(--blue)}

/* choose */
.choose-photo{left:0;top:3220px;width:611px;height:462px;background:linear-gradient(135deg,#8a2a22 0%,#e9e0d4 50%,#f3efe8 100%)}
.choose-panel{left:611px;top:3220px;width:589px;height:462px;background:#9e9e9e}
.choose-title{left:484px;top:3420px;font-size:29px;color:#111}
.choose-box{left:780px;top:3260px;width:200px;height:200px;background:linear-gradient(180deg,#e0a030 0%,#c9925a 40%,#b07a48 100%)}
.choose-sub{left:611px;width:589px;top:3548px;text-align:center;color:var(--white);font-size:22px}

/* packages */
.pack-photo{left:166px;top:3733px;width:454px;height:424px;background:linear-gradient(180deg,#a88060 0%,#c0a080 45%,#2a4aa0 75%,#c02a3a 100%);border-radius:12px}
.pack-title{left:644px;top:3786px;font-size:34px}
.pack-copy{left:644px;width:400px}

/* footer */
.footer{left:0;top:4196px;width:1200px;height:338px;background:var(--footer)}
.foot-links{left:175px;top:4248px;list-style:none}
.foot-links li{font-size:17px;line-height:35px;color:#333}
.signup{left:553px;top:4248px;font-size:21px;color:#333}
.email{left:553px;top:4300px;width:454px;height:34px;border-bottom:2px solid #555;display:flex;justify-content:space-between;align-items:center;font-size:15px;color:#444}
.social{left:166px;top:4440px;display:flex;gap:10px}
.social span{width:36px;height:36px;border-radius:50%;border:2px solid #333}
.copy{left:499px;top:4451px;font-size:13px;color:#444}
.pay{left:877px;top:4450px;display:flex;gap:14px;font-size:12px;font-weight:700;color:#444}
.ver{left:1160px;top:4505px;font-size:12px;color:#666}
</style>
</head>
<body>

<header class="hero" role="img" aria-label="Photo of a puppy playing with a red toy on a wooden floor">
  <svg class="abs menu" width="44" height="24" viewBox="0 0 44 24"><g stroke="#fff" stroke-width="3"><line x1="0" y1="2" x2="44" y2="2"/><line x1="0" y1="12" x2="44" y2="12"/><line x1="0" y1="22" x2="44" y2="22"/></g></svg>
  <div class="brand"><b>PUP</b> SNACK DEN</div>
  <svg class="abs bag" width="36" height="34" viewBox="0 0 36 34"><path d="M10 11 V7 a8 8 0 0 1 16 0 V11" fill="none" stroke="#fff" stroke-width="3"/><rect x="2" y="11" width="32" height="22" fill="#fff"/></svg>
  <h1 class="hero-title">Vivamus porttitor purus nisi eleifend<br>libero tempus libero lectus</h1>
  <div class="dots"><span class="on"></span><span></span><span></span><span></span></div>
</header>

<section class="about">
  <div class="photo about-photo" role="img" aria-label="Photo of a dog in a cap holding a cardboard box"></div>
  <div class="rule blue" style="left:590px;top:710px;width:92px"></div>
  <h2 class="abs" style="left:590px;top:720px">About Pup Snack Den</h2>
  <p class="abs" style="left:590px;top:780px;width:450px">Praesent elementum elit at tellus nec ultricies sit amet porttitor mattis enim in massa libero interdum nec.</p>
  <p class="abs" style="left:590px;top:840px;width:450px">Interdum vel blandit sed nulla in ullamcorper est eget tempor cursus neque mi consectetur mi a ultricies massa est sed nisl class aptent taciti sociosqu ad litora torquent per conubia nostra per inceptos hymenaeos proin nulla arcu nonumm.</p>
</section>

<section class="photo video" role="img" aria-label="Photo of a fluffy puppy sitting in a clear tub of toys">
</section>
<p class="video-quote">“Fusce ultricies orci ac feugiat suscipit leo massa sodales velit et scelerisque mi tortor at ipsum cligula augue”</p>
<svg class="abs play" width="92" height="92" viewBox="0 0 92 92"><circle cx="46" cy="46" r="44" fill="rgba(255,255,255,.15)" stroke="#fff" stroke-width="3"/><path d="M36 28 L64 46 L36 64 Z" fill="#fff"/></svg>

<section class="why">
  <div class="rule orange" style="left:554px;top:1597px;width:92px"></div>
  <h2 class="abs center" style="left:0;width:1200px;top:1614px;font-size:32px">Why Choose Our Boxes</h2>
  <p class="abs center" style="left:250px;width:700px;top:1670px">Praesent elementum elit at tellus nec ultricies sit amet porttitor mattis enim in massa.</p>
  <p class="abs center" style="left:250px;width:700px;top:1710px">Interdum vel blandit sed nulla in ullamcorper est eget tempor cursus neque mi consectetur mi a ultricies massa est sed nisl class aptent taciti sociosqu ad litora torquent per conubia nostra per inceptos hymenaeos proin nulla arcu nonumm.</p>
</section>

<div class="photo tile left" role="img" aria-label="Blue tinted photo of a white dog beside a box of treats">
  <svg width="76" height="70" viewBox="0 0 76 70"><circle cx="38" cy="38" r="28" fill="none" stroke="#fff" stroke-width="3"/><path d="M38 22 l4 9 10 1 -8 6 3 10 -9-6 -9 6 3-10 -8-6 10-1z" fill="#fff"/></svg>
  <div class="tile-label">OUR BEST BRANDS</div>
</div>
<div class="photo tile right" role="img" aria-label="Photo of a terrier carrying a colourful toy on grass">
  <svg width="76" height="76" viewBox="0 0 76 76"><circle cx="38" cy="38" r="33" fill="none" stroke="#fff" stroke-width="4"/><path d="M22 39 L33 50 L55 27" fill="none" stroke="#fff" stroke-width="5"/></svg>
  <div class="tile-label">BEST QUALITY PRODUCTS</div>
</div>

<section class="abs band">
  <p class="band-quote">“Class aptent taciti sociosqu ad litora torquent per conubia nostra per inceptos<br>hymenaeos Proin nulla arcu nonummy luctus dictum ege”</p>
  <div class="band-author">By Author Name</div>
</section>

<section class="shop">
  <p class="abs lead">Morbi diam mauris viverra in gravida eu mattis in ante Morbi eget arcu Morbi porta libero id ullamcorper nonummy nibh ligula pulvinar metus eget</p>
  <div class="photo bone" role="img" aria-label="Pink toy bone"></div>
  <div class="photo rope" role="img" aria-label="Pink rope toy"></div>
  <div class="abs box-frame"></div>
  <div class="photo pup-peek" role="img" aria-label="Puppy peeking over the frame"></div>
  <div class="photo product" role="img" aria-label="Open cardboard box filled with dog food and toys"></div>
  <h3 class="abs box-title">Pup Snack Box</h3>
  <p class="abs box-copy">Ullamcorper est eget tempor cursus neque mi consectetur mi a ultricies massa est sed nisl class aptent taciti sociosqu ad litora torquent.</p>
  <div class="btn orange" style="left:547px;top:3065px;width:142px;height:40px">BUY NOW</div>
</section>

<section class="choose">
  <div class="photo choose-photo" role="img" aria-label="Photo of a happy terrier on a rug by a festive tree"></div>
  <div class="abs choose-panel"></div>
  <div class="photo choose-box" role="img" aria-label="Cardboard box with treat packs"></div>
  <h2 class="abs choose-title">Choose Your Box</h2>
  <div class="abs choose-sub">Your Box Tittle here</div>
  <div class="btn blue" style="left:789px;top:3591px;width:154px;height:40px">CLICK HERE</div>
</section>

<section class="packages">
  <div class="photo pack-photo" role="img" aria-label="Photo of a shepherd dog with a toy bone and leash"></div>
  <h2 class="abs pack-title">Our Box Packages</h2>
  <p class="abs pack-copy" style="top:3845px">Praesent elementum elit at tellus nec ultricies sit amet porttitor mattis enim in massa.</p>
  <p class="abs pack-copy" style="top:3905px">Interdum vel blandit sed nulla in ullamcorper est eget tempor cursus neque mi consectetur mi a ultricies massa est sed nisl class aptent taciti sociosqu ad litora torquent per conubia nostra per inceptos.</p>
  <div class="btn orange" style="left:644px;top:4030px;width:157px;height:45px">CLICK HERE</div>
</section>

<footer class="abs footer"></footer>
<ul class="abs foot-links"><li>CONTACT US</li><li>TERM OF USE</li><li>PRIVACY</li><li>POLICY REFUND</li></ul>
<div class="abs signup">SIGN UP FOR UPDATES</div>
<div class="abs email"><span>Email address</span><span>OK</span></div>
<div class="abs social"><span></span><span></span><span></span><span></span></div>
<div class="abs copy">© 2017 Company Name  All right reserved</div>
<div class="abs pay"><span>Talvo</span><span>Quenby</span><span>Orlix</span><span>Pemtra</span></div>
<div class="abs ver">X14</div>

</body>
</html>
```